Bloom Path! A website showcasing who I am as a person

Bloom Path started out as idea for me to better myself as a person and work on small projects that would help me grow as a person. Now I want to build a website showcasing "Bloom Path." I want the website to showcase who I am and how I have grown both professionally and personally. I can build the raw code of the website on my own but I am not really much of a designer. I am looking for a design where I can write and post blogs, articles and share my thoughts. A little about myself and the ideas and interests that I want to share
What is Bloom Path
Who I am
Background - Professional
Brand Marketing
Email Automation
Hiking
Rock Climbing
Traveling
Exercising and Transformation
"Personal Thoughts"
Hopefully this is enough information to get people started on some designs.
Work
3 page

```html
<!DOCTYPE html>
<html lang="en">
<head>
<meta charset="utf-8">
<title>Rohan Mehta — Bloom Path</title>
<link href="https://fonts.googleapis.com/css2?family=Raleway:wght@500;600;700;800&family=Mulish:wght@400;600&display=swap" rel="stylesheet">
<style>
:root{
  --blue:#2f70b3;
  --blue-dark:#245e9a;
  --ink:#2b2b2b;
  --body:#4a4a4a;
  --muted:#6d6d6d;
  --band:#f4f4f4;
  --white:#ffffff;
  --hero-a:#5b4636;
  --hero-b:#9a8f86;
  --hero-c:#c98a4a;
}
*{margin:0;padding:0;box-sizing:border-box}
html,body{width:1200px;height:2586px;overflow:hidden;background:var(--white)}
body{position:relative;font-family:'Mulish',sans-serif;color:var(--body)}
.abs{position:absolute}
h1,h2,h3,.brand{font-family:'Raleway',sans-serif}

/* Hero */
.hero{left:0;top:0;width:1200px;height:600px;
  background:linear-gradient(120deg,var(--hero-a) 0%,#7d6a5c 30%,var(--hero-b) 50%,#7a5a3e 75%,var(--hero-c) 100%)}
.hero-shade{inset:0;background:rgba(0,0,0,.25)}
.brand{left:74px;top:30px;color:var(--white);font-size:27px;font-weight:700;letter-spacing:.5px}
.header-rule{left:74px;top:81px;width:1052px;height:1px;background:rgba(255,255,255,.55)}
.menu{left:1094px;top:34px}
.hero-title{left:0;top:244px;width:1200px;text-align:center;color:var(--white);font-size:50px;font-weight:800;letter-spacing:1px}
.hero-sub{left:0;top:304px;width:1200px;text-align:center;color:var(--white);font-family:'Raleway',sans-serif;font-weight:500;font-size:32px;line-height:40px}
.dots{left:563px;top:553px;display:flex;gap:8px}
.dots span{width:12px;height:12px;border-radius:50%;background:var(--white)}
.dots span.on{background:var(--blue);box-shadow:0 0 0 2px var(--white)}

/* Shared */
.section-title{color:var(--blue);font-size:27px;font-weight:700;letter-spacing:.5px}
.text{font-size:14.5px;line-height:23px;color:var(--body)}
.btn{display:inline-block;height:37px;width:138px;border-radius:19px;background:var(--blue);color:var(--white);
  font-family:'Raleway',sans-serif;font-weight:700;font-size:13px;letter-spacing:.5px;text-align:center;line-height:37px}

/* Who I am */
.who{left:74px;top:650px;width:1052px;height:276px;border-radius:34px;background:var(--band)}
.portrait{left:100px;top:672px;width:228px;height:228px;border-radius:50%;border:4px solid var(--white);
  background:linear-gradient(160deg,#e9e6e2,#c9b8a3 60%,#8a7660);box-shadow:0 0 0 1px #ddd}
.who-title{left:390px;top:680px}
.who-text{left:390px;top:727px;width:716px}
.who-btn{left:390px;top:856px}

/* Bloom Path */
.what-title{left:74px;top:970px}
.what-text{left:74px;top:1021px;width:600px}
.what-btn{left:74px;top:1167px}
.what-img{left:703px;top:976px;width:423px;height:248px;border-radius:34px;
  background:linear-gradient(135deg,#cfd7de,#e8e1e6 45%,#9aa7b3 75%,#6e6a63)}

/* Growth */
.grow{left:0;top:1276px;width:1200px;height:310px;background:var(--band)}
.grow-title{left:0;top:1312px;width:1200px;text-align:center}
.grow-img{width:179px;height:147px;border-radius:24px;top:1379px}
.grow-img.pro{left:74px;background:linear-gradient(135deg,#e6e8ec,#b9c4d2 60%,#8898b0)}
.grow-img.thoughts{left:615px;background:linear-gradient(135deg,#3a3a3a,#262626 60%,#4a463f)}
.item-title{font-family:'Raleway',sans-serif;font-weight:700;font-size:17.5px;color:var(--ink);top:1374px}
.item-text{top:1404px;width:320px}
.item-btn{top:1489px}

/* Interests */
.card{top:1631px;width:241px;height:284px;border-radius:30px;background:var(--blue);color:var(--white);text-align:center}
.card svg{position:absolute;left:50%;transform:translateX(-50%);top:32px}
.card h3{position:absolute;left:0;right:0;top:120px;font-size:16px;font-weight:700;letter-spacing:.3px}
.card p{position:absolute;left:16px;right:16px;top:156px;font-size:14px;line-height:23px}

/* Blogs */
.blogs{left:0;top:1974px;width:1200px;height:503px;background:var(--band)}
.blogs-title{left:0;top:2013px;width:1200px;text-align:center}
.post-img{top:2074px;width:331px;height:174px;border-radius:28px}
.post-img.desk{background:linear-gradient(135deg,#8b6a45,#c8b08a 45%,#e9e3d6 70%,#6f8a5a)}
.post-img.city{background:linear-gradient(135deg,#6f8aa0,#d9c9a8 50%,#f3a23a 80%,#6a5a40)}
.post-img.tech{background:linear-gradient(135deg,#d8d2cc,#b7aaa2 50%,#6e5d58)}
.post-title{top:2268px;width:331px;font-family:'Raleway',sans-serif;font-weight:700;font-size:17.5px;line-height:23px;color:var(--ink)}
.post-text{top:2324px;width:331px}
.post-link{top:2405px;font-size:13px;font-weight:600;color:var(--blue)}

/* Footer */
.copy{left:74px;top:2512px;font-size:12.5px;line-height:22px;color:var(--muted)}
.follow{left:913px;top:2508px;font-family:'Raleway',sans-serif;font-weight:700;font-size:13px;color:var(--muted);letter-spacing:.5px}
.socials{left:913px;top:2532px;display:flex;gap:17px}
.socials span{width:20px;height:20px;border-radius:50%;background:#8a8a8a}
</style>
</head>
<body>

<section class="abs hero" role="img" aria-label="Photo of a climber hanging on a sunlit rock face"></section>
<div class="abs hero-shade"></div>
<div class="abs brand">ROHAN MEHTA</div>
<div class="abs header-rule"></div>
<svg class="abs menu" width="24" height="22" viewBox="0 0 24 22" aria-label="Menu">
  <rect y="1" width="24" height="3.5" rx="1" fill="#fff"/>
  <rect y="9" width="24" height="3.5" rx="1" fill="#fff"/>
  <rect y="17" width="24" height="3.5" rx="1" fill="#fff"/>
</svg>
<h1 class="abs hero-title">LOREM IPSUM DOLOR</h1>
<p class="abs hero-sub">Vestibulum ante ipsum primis in faucibus<br>orci luctus et ultrices posuere</p>
<div class="abs dots"><span class="on"></span><span></span><span></span><span></span></div>

<!-- Who I am -->
<div class="abs who"></div>
<div class="abs portrait" role="img" aria-label="Portrait photo of Rohan in a light blazer"></div>
<h2 class="abs section-title who-title">WHO I AM</h2>
<p class="abs text who-text">Aliquam molestie, mi et imperdiet euismod, dui purus auctor tellus, et interdum lacus lectus et ante. Sed accumsan sollicitudin sapien, sit amet adipiscing turpis gravida ac. In congue, neque ac lobortis volutpat, libero mauris varius mi, vitae suscipit ipsum ligula vitae risus. Duis aliquam nibh a dui iaculis viverra id a velit. Vivamus egestas risus in magna varius commodo. Sed semper viverra egestas. Etiam pretium porttitor lectus, vel ornare neque porta volutpat.</p>
<a class="abs btn who-btn">READ MORE</a>

<!-- What is Bloom Path -->
<h2 class="abs section-title what-title">WHAT IS BLOOM PATH ?</h2>
<p class="abs text what-text">Aliquam molestie, mi et imperdiet euismod, dui purus auctor tellus, et interdum lacus lectus et ante. Sed accumsan sollicitudin sapien, sit amet adipiscing turpis gravida ac. In congue, neque ac lobortis volutpat, libero mauris varius mi, vitae suscipit ipsum ligula vitae risus. Duis aliquam nibh a dui iaculis viverra id a velit. Vivamus egestas risus in magna varius commodo.</p>
<a class="abs btn what-btn">READ MORE</a>
<div class="abs what-img" role="img" aria-label="Photo of a team meeting around a table with a projected chart"></div>

<!-- How I have grown -->
<div class="abs grow"></div>
<h2 class="abs section-title grow-title">HOW I HAVE GROWN</h2>
<div class="abs grow-img pro" role="img" aria-label="Photo of colleagues in a business meeting"></div>
<h3 class="abs item-title" style="left:283px">PROFESSIONAL</h3>
<p class="abs text item-text" style="left:283px">Suspendisse lobortis turpis in odio blandit ac interdum lorem euismod. Etiam risus massa, vulputate eu...</p>
<a class="abs btn item-btn" style="left:283px">READ MORE</a>
<div class="abs grow-img thoughts" role="img" aria-label="Photo of a man thinking in front of a chalkboard"></div>
<h3 class="abs item-title" style="left:822px">PERSONAL THOUGHTS</h3>
<p class="abs text item-text" style="left:822px">Suspendisse lobortis turpis in odio blandit ac interdum lorem euismod. Etiam risus massa, vulputate eu...</p>
<a class="abs btn item-btn" style="left:822px">READ MORE</a>

<!-- Interests -->
<div class="abs card" style="left:74px">
  <svg width="100" height="66" viewBox="0 0 100 66" aria-hidden="true">
    <rect x="14" y="2" width="72" height="50" rx="4" fill="none" stroke="#fff" stroke-width="5"/>
    <path d="M2 56h96v3a5 5 0 0 1-5 5H7a5 5 0 0 1-5-5z" fill="#fff"/>
    <path d="M38 18h16l12 12-10 10-12-12h-6z" fill="#fff"/>
    <circle cx="44" cy="24" r="2.5" fill="#2f70b3"/>
  </svg>
  <h3>BRAND MARKETING</h3>
  <p>Suspendisse lobortis turpis in odio blandit ac interdum lorem euismod egestas risus in magna varius..</p>
</div>
<div class="abs card" style="left:344px">
  <svg width="84" height="66" viewBox="0 0 84 66" aria-hidden="true">
    <rect x="2" y="4" width="80" height="58" rx="8" fill="#fff"/>
    <path d="M6 10l36 28 36-28" fill="none" stroke="#2f70b3" stroke-width="5"/>
  </svg>
  <h3>EMAIL AUTOMATION</h3>
  <p>Suspendisse lobortis turpis in odio blandit ac interdum lorem euismod egestas risus in magna varius..</p>
</div>
<div class="abs card" style="left:615px">
  <svg width="66" height="66" viewBox="0 0 66 66" aria-hidden="true">
    <g transform="rotate(-45 33 33)">
      <path d="M30 4c0-3 6-3 6 0v20l24 14v6l-24-7v15l7 5v5l-10-3-10 3v-5l7-5V37L6 44v-6l24-14z" fill="#fff"/>
    </g>
  </svg>
  <h3>TRAVELING</h3>
  <p>Suspendisse lobortis turpis in odio blandit ac interdum lorem euismod egestas risus in magna varius..</p>
</div>
<div class="abs card" style="left:885px">
  <svg width="80" height="66" viewBox="0 0 80 66" aria-hidden="true">
    <path d="M2 64L30 14l14 22 8-12 26 40z" fill="#fff"/>
    <path d="M24 25l6-11 6 10-6 5z" fill="#2f70b3"/>
  </svg>
  <h3>HIKING</h3>
  <p>Suspendisse lobortis turpis in odio blandit ac interdum lorem euismod egestas risus in magna varius..</p>
</div>

<!-- Blogs & Articles -->
<div class="abs blogs"></div>
<h2 class="abs section-title blogs-title">BLOGS &amp; ARTICLES</h2>

<div class="abs post-img desk" style="left:74px" role="img" aria-label="Photo of a desk with notebook, glasses and coffee"></div>
<h3 class="abs post-title" style="left:74px">NAM FERMENTUM VESTIBULUM PURUS ID ALIQUET.</h3>
<p class="abs text post-text" style="left:74px">Suspendisse lobortis turpis in odio blandit ac interdum lorem euismod. Etiam risus massa, vulputate eu...</p>
<a class="abs post-link" style="left:74px">Continue Reading</a>

<div class="abs post-img city" style="left:435px" role="img" aria-label="Photo of a traveller walking past glass buildings at sunset"></div>
<h3 class="abs post-title" style="left:435px">NAM FERMENTUM VESTIBULUM PURUS ID ALIQUET.</h3>
<p class="abs text post-text" style="left:435px">Suspendisse lobortis turpis in odio blandit ac interdum lorem euismod. Etiam risus massa, vulputate eu...</p>
<a class="abs post-link" style="left:435px">Continue Reading</a>

<div class="abs post-img tech" style="left:795px" role="img" aria-label="Photo of hands typing on a laptop with digital icons"></div>
<h3 class="abs post-title" style="left:795px">NAM FERMENTUM VESTIBULUM PURUS ID ALIQUET.</h3>
<p class="abs text post-text" style="left:795px">Suspendisse lobortis turpis in odio blandit ac interdum lorem euismod. Etiam risus massa, vulputate eu...</p>
<a class="abs post-link" style="left:795px">Continue Reading</a>

<!-- Footer -->
<p class="abs copy">Copyright © 2017. Company Name.<br>All Right Reserved</p>
<div class="abs follow">FOLLOW ME</div>
<div class="abs socials" aria-label="Social links">
  <span></span><span></span><span></span><span></span><span></span><span></span>
</div>

</body>
</html>
```